Business card for law firm

Need business card for new law firm. Think confident, authoritative, conservative, but not stuffy or old-fashioned.

Contact Information for Business Card

Content for card - logo (uploaded), plus the following:

Paul Whitcombe (larger font)
Managing Partner (larger font, but not as large as name)
Level 9, 7 Ferris Lane
Sydney NSW 2000
Main Tel 02 9364 2710
Direct Tel 02 8472 3159
Email paul@qvlegal.com.au
www.qvlegal.com.au

Letterhead design should include logo plus:
Level 9, 7 Ferris Lane
Sydney NSW 2000
Tel 02 8472 3159
www.qvlegal.com.au

```html
<!DOCTYPE html>
<html lang="en">
<head>
<meta charset="utf-8">
<title>Quayvale Legal — Business Card</title>
<link rel="stylesheet" href="https://fonts.googleapis.com/css2?family=Cinzel:wght@500&family=Roboto:wght@400;700&display=swap">
<style>
  :root {
    --backdrop: #d9dadc;
    --navy: #0f1f5c;
    --navy-deep: #0b1950;
    --ink: #111111;
    --paper: #ffffff;
    --white: #ffffff;
  }
  * { box-sizing: border-box; margin: 0; padding: 0; }
  html, body {
    width: 1200px;
    height: 1000px;
    overflow: hidden;
    background: var(--backdrop);
  }
  .canvas {
    position: relative;
    width: 1200px;
    height: 1000px;
  }
  .card {
    position: absolute;
    left: 290px;
    width: 620px;
    height: 354px;
    border-radius: 24px;
    box-shadow: 0 10px 28px rgba(0,0,0,0.18);
    display: flex;
    flex-direction: column;
    align-items: center;
    text-align: center;
  }
  .card--front {
    top: 90px;
    background: linear-gradient(160deg, var(--navy) 0%, var(--navy-deep) 100%);
    color: var(--white);
    justify-content: center;
  }
  .card--back {
    top: 540px;
    background: var(--paper);
    color: var(--ink);
    padding-top: 44px;
  }
  .brand {
    display: flex;
    align-items: center;
    gap: 14px;
    font-family: "Cinzel", serif;
    font-weight: 500;
    letter-spacing: 0.06em;
  }
  .brand__square {
    width: 22px;
    height: 22px;
    background: currentColor;
  }
  .card--front .brand { font-size: 44px; }
  .card--back .brand { font-size: 34px; color: var(--ink); }
  .card--back .brand__square { background: var(--navy); width: 18px; height: 18px; }
  .front__rule {
    width: 80px;
    height: 2px;
    background: var(--white);
    margin: 26px 0 16px;
  }
  .front__web {
    font-family: "Roboto", sans-serif;
    font-size: 15px;
    letter-spacing: 0.04em;
  }
  .person__name {
    margin-top: 26px;
    font-family: "Roboto", sans-serif;
    font-weight: 700;
    font-size: 22px;
    color: var(--navy);
    letter-spacing: 0.01em;
  }
  .person__role {
    font-family: "Roboto", sans-serif;
    font-size: 17px;
    color: var(--ink);
    margin-top: 2px;
  }
  .back__rule {
    width: 540px;
    height: 1.5px;
    background: var(--navy);
  }
  .back__rule--top { margin-top: 10px; }
  .back__rule--bottom { margin-top: 14px; }
  .contact {
    list-style: none;
    font-family: "Roboto", sans-serif;
    font-size: 14px;
    line-height: 1.45;
    margin-top: 10px;
    color: var(--ink);
  }
  .contact__label {
    font-weight: 700;
    color: var(--navy);
  }
  .contact__gap { margin-left: 10px; }
  .back__web {
    margin-top: 8px;
    font-family: "Roboto", sans-serif;
    font-weight: 700;
    font-size: 14px;
    color: var(--ink);
  }
</style>
</head>
<body>
<main class="canvas">
  <section class="card card--front" aria-label="Card front">
    <div class="brand"><span class="brand__square"></span>Quayvale Legal</div>
    <div class="front__rule"></div>
    <div class="front__web">www.qvlegal.com.au</div>
  </section>

  <section class="card card--back" aria-label="Card back">
    <div class="brand"><span class="brand__square"></span>Quayvale Legal</div>
    <h1 class="person__name">PAUL WHITCOMBE</h1>
    <p class="person__role">Managing Partner</p>
    <div class="back__rule back__rule--top"></div>
    <ul class="contact">
      <li><span class="contact__label">Main Tel</span> 02 9364 2710<span class="contact__gap"></span><span class="contact__label">Direct Tel</span> 02 8472 3159</li>
      <li><span class="contact__label">Email</span> paul@qvlegal.com.au</li>
      <li><span class="contact__label">Address</span> Level 9, 7 Ferris Lane Sydney NSW 2000</li>
    </ul>
    <p class="back__web">www.qvlegal.com.au</p>
    <div class="back__rule back__rule--bottom"></div>
  </section>
</main>
</body>
</html>
```